Small Business Broker Business Card Design

A business card design for a small business brokerage, which is a financial service, not unlike real estate brokerage, but for small businesses such as laundromats, pizza shops, restaurants, cleaners etc. The designs should all be simple, more conservative in nature, using the colors and font of the logo. Again, think real estate Brokerage as a business context
Contact Information for Business Card
Name: Glen R. Harlow. Title: Small Business Advisor. Email: g.harlow@bayfieldcapitalworks.example. Mobile: (555) 274-3918. Office: (555) 806-2147. www.bayfieldcapitalworks.example

```html
<!DOCTYPE html>
<html lang="en">
<head>
<meta charset="utf-8">
<title>Bayfield Capital Works – Business Card</title>
<link rel="stylesheet" href="https://fonts.googleapis.com/css2?family=Montserrat:wght@600;700&family=Arimo:wght@400&display=swap">
<style>
  :root {
    --navy: #173a6e;
    --navy-deep: #12305c;
    --navy-light: #2c5591;
    --green: #8cc63f;
    --white: #ffffff;
    --ink: #333a44;
    --stage: #3a3b3d;
  }
  * { box-sizing: border-box; margin: 0; padding: 0; }
  html, body { width: 1200px; height: 900px; overflow: hidden; }
  body {
    background: var(--stage);
    display: flex; flex-direction: column; align-items: center; justify-content: center;
    gap: 40px;
    font-family: "Arimo", Arial, sans-serif;
  }
  .card {
    position: relative;
    width: 680px; height: 389px;
    border-radius: 18px;
    overflow: hidden;
  }
  .card-back { background: var(--navy); }
  .back-pattern {
    position: absolute; inset: 0;
    background: linear-gradient(200deg, var(--navy-light) 0%, var(--navy) 45%, var(--navy-deep) 100%);
  }
  .back-mark {
    position: absolute; right: 60px; bottom: 60px;
    width: 34px; height: 34px; background: var(--white);
  }
  .card-front { background: var(--white); }

  .brand {
    position: absolute; left: 190px; top: 62px; width: 380px;
    display: flex; flex-direction: column; align-items: center;
  }
  .brand-square { width: 54px; height: 54px; background: var(--navy); margin-bottom: 16px; }
  .brand-name {
    font-family: "Montserrat", Arial, sans-serif; font-weight: 700;
    font-size: 21px; letter-spacing: 0.5px; color: var(--navy); text-transform: uppercase;
  }
  .brand-tagline {
    font-family: "Montserrat", Arial, sans-serif; font-weight: 600;
    font-size: 9.5px; letter-spacing: 1.6px; color: var(--green); text-transform: uppercase;
    margin-top: 3px;
  }

  .person { position: absolute; left: 70px; top: 240px; width: 240px; text-align: right; }
  .person-name {
    font-family: "Montserrat", Arial, sans-serif; font-weight: 700;
    font-size: 27px; color: var(--navy); text-transform: uppercase; letter-spacing: 0.5px;
  }
  .person-title { font-size: 16px; color: var(--ink); margin-top: 2px; }

  .divider { position: absolute; left: 330px; top: 205px; width: 1px; height: 100px; background: var(--navy); }

  .contacts { position: absolute; left: 348px; top: 205px; list-style: none; }
  .contacts li {
    display: flex; align-items: center; gap: 10px;
    font-size: 15px; color: var(--ink); height: 25px;
  }
  .contacts svg { width: 13px; height: 13px; flex: none; }

  .band { position: absolute; bottom: 0; height: 20px; }
  .band-navy { left: 0; width: 57%; background: var(--navy); }
  .band-green { right: 0; width: 43%; background: var(--green); }
  .band-joint {
    position: absolute; left: calc(57% - 14px); bottom: 3px;
    width: 28px; height: 28px; background: var(--white); border: 3px solid var(--navy);
  }
</style>
</head>
<body>

<section class="card card-back" aria-label="Card back">
  <div class="back-pattern" role="img" aria-label="Embossed repeating chevron pattern in tones of navy blue"></div>
  <div class="back-mark"></div>
</section>

<section class="card card-front" aria-label="Card front">
  <div class="brand">
    <div class="brand-square"></div>
    <div class="brand-name">Bayfield Capital Works, Inc</div>
    <div class="brand-tagline">Confidently buy or sell a local business today</div>
  </div>

  <div class="person">
    <div class="person-name">Glen R. Harlow</div>
    <div class="person-title">Small Business Advisor</div>
  </div>

  <div class="divider"></div>

  <ul class="contacts">
    <li>
      <svg viewBox="0 0 16 16" aria-hidden="true"><path fill="#8cc63f" d="M1 5c0-2 2-3 7-3s7 1 7 3v1.5h-3.5V5H4.5v1.5H1zM4 8h8l2 6H2z"/></svg>
      (555) 806-2147
    </li>
    <li>
      <svg viewBox="0 0 16 16" aria-hidden="true"><rect x="4" y="1" width="8" height="14" rx="1.5" fill="none" stroke="#8cc63f" stroke-width="1.6"/><circle cx="8" cy="12.5" r="0.9" fill="#8cc63f"/></svg>
      (555) 274-3918
    </li>
    <li>
      <svg viewBox="0 0 16 16" aria-hidden="true"><rect x="1" y="3" width="14" height="10" fill="#8cc63f"/><path d="M1 3l7 6 7-6" fill="none" stroke="#fff" stroke-width="1.2"/></svg>
      g.harlow@bayfieldcapitalworks.example
    </li>
    <li>
      <svg viewBox="0 0 16 16" aria-hidden="true"><circle cx="8" cy="8" r="6.5" fill="none" stroke="#8cc63f" stroke-width="1.6"/><path d="M1.5 8h13M8 1.5c-3 3.5-3 9.5 0 13M8 1.5c3 3.5 3 9.5 0 13" fill="none" stroke="#8cc63f" stroke-width="1.2"/></svg>
      www.bayfieldcapitalworks.example
    </li>
  </ul>

  <div class="band band-navy"></div>
  <div class="band band-green"></div>
  <div class="band-joint"></div>
</section>

</body>
</html>
```